real esate business card with company logo and name

we need a business card design for a real esate company

The company name is Walsh & Brand Pty Ltd, and we have our logo designed and will upload. We want classic or moden feel. Black or white background. looks more textured. Should include folowinginformations
Owen Walsh and Lucy Brand
Sales Agents & Onsite Manager
p: 07 5948 2063
F: 07 5948 2174
M:0431 857 219
3/42 Marlow Crescent, FERNLEA QLD 4213

We want this business card looks professonal. Thank you in advance.

Industry/Entity Type

Real Estate Agent

Contact Information for Business Card

Owen Walsh and Lucy Brand
Onsite Manager & Sales Agents
p: 07 5948 2063
M:0431 857 219

Font styles to use
Serif

Colors
000000
fbfbfb
333333
959595

Requirements
Must have
• company logo and name, black or white back ground

```html
<!DOCTYPE html>
<html lang="en">
<head>
<meta charset="utf-8">
<title>Walsh &amp; Brand Pty Ltd – Business Card</title>
<link rel="stylesheet" href="https://fonts.googleapis.com/css2?family=Lato:wght@400;700&family=Oswald:wght@400&display=swap">
<style>
  :root {
    --backdrop: #333333;
    --card-black: #000000;
    --band-grey: #cfcfd0;
    --mark-grey: #959595;
    --ink: #000000;
    --paper: #fbfbfb;
  }
  * { box-sizing: border-box; margin: 0; padding: 0; }
  html, body {
    width: 1200px;
    height: 1086px;
    overflow: hidden;
    background: var(--backdrop);
  }
  .card {
    position: absolute;
    left: 254px;
    width: 677px;
    background: var(--card-black);
    overflow: hidden;
  }
  .card--front { top: 126px; height: 387px; }
  .card--back  { top: 586px; height: 385px; }

  .brand-square {
    position: absolute;
    left: 50%;
    transform: translateX(-50%);
    background: var(--mark-grey);
  }
  .card--front .brand-square { top: 38px; width: 130px; height: 130px; }
  .card--back  .brand-square { top: 62px; width: 200px; height: 200px; }

  .brand-name {
    position: absolute;
    left: 0;
    width: 100%;
    text-align: center;
    font-family: "Oswald", sans-serif;
    font-weight: 400;
    color: var(--mark-grey);
    text-transform: uppercase;
    letter-spacing: 0.02em;
    white-space: nowrap;
  }
  .card--front .brand-name { top: 188px; font-size: 19px; }
  .card--back  .brand-name { top: 298px; font-size: 30px; }

  .info-band {
    position: absolute;
    left: 0;
    top: 243px;
    width: 100%;
    height: 121px;
    background: var(--band-grey);
    font-family: "Lato", sans-serif;
    color: var(--ink);
  }
  .info-band__divider {
    position: absolute;
    left: 339px;
    top: 0;
    width: 3px;
    height: 100%;
    background: var(--card-black);
  }
  .agent {
    position: absolute;
    right: 354px;
    top: 6px;
    text-align: right;
  }
  .agent__name { font-size: 28px; font-weight: 700; line-height: 1.2; }
  .agent__role { font-size: 19px; font-weight: 400; line-height: 1.2; }

  .contact {
    position: absolute;
    left: 363px;
    top: 5px;
    list-style: none;
  }
  .contact__line {
    display: flex;
    align-items: center;
    font-size: 18px;
    line-height: 22.5px;
  }
  .contact__icon { width: 14px; height: 14px; margin-right: 5px; flex: none; }
  .address {
    position: absolute;
    left: 363px;
    top: 76px;
    font-size: 15px;
    line-height: 20px;
    font-style: normal;
  }
</style>
</head>
<body>

<section class="card card--front" aria-label="Business card front">
  <div class="brand-square"></div>
  <p class="brand-name">Walsh &amp; Brand Pty Ltd.</p>

  <div class="info-band">
    <div class="agent">
      <p class="agent__name">Owen Walsh</p>
      <p class="agent__role">Sales Agents</p>
    </div>
    <div class="info-band__divider"></div>
    <ul class="contact">
      <li class="contact__line">
        <svg class="contact__icon" viewBox="0 0 14 14" aria-hidden="true"><rect x="3.5" y="1" width="7" height="12" rx="1.2" fill="none" stroke="#000" stroke-width="1.4"/><line x1="6" y1="11" x2="8" y2="11" stroke="#000" stroke-width="1.2"/></svg>
        0431 857 219
      </li>
      <li class="contact__line">
        <svg class="contact__icon" viewBox="0 0 14 14" aria-hidden="true"><path d="M1 5 Q7 0 13 5 L11 6.5 L9.5 5 L4.5 5 L3 6.5 Z" fill="#000"/><rect x="3" y="7" width="8" height="6" rx="1" fill="#000"/></svg>
        07 5948 2063
      </li>
      <li class="contact__line">
        <svg class="contact__icon" viewBox="0 0 14 14" aria-hidden="true"><rect x="4" y="1" width="6" height="4" fill="#000"/><rect x="1" y="5" width="12" height="6" rx="1" fill="#000"/><rect x="4" y="9" width="6" height="4" fill="#000" stroke="#cfcfd0" stroke-width="0.8"/></svg>
        07 5948 2174
      </li>
    </ul>
    <address class="address">
      3/42 Marlow Crescent<br>
      FERNLEA QLD 4213
    </address>
  </div>
</section>

<section class="card card--back" aria-label="Business card back">
  <div class="brand-square"></div>
  <p class="brand-name">Walsh &amp; Brand Pty Ltd.</p>
</section>

</body>
</html>
```